Wavelink Earphone Packaging Design

We want to use the packaging for 4-5 of our Wavelink Earphone series (Picture enclosed) and hence we would not like to put any product pictures on the packaging.

Material: E-Flute Paper box
Type: Window Box style
Design features we prefer: Colorful, creative, trendy, High tech.
Requirement: AI file is preferred
Size of Packaging: (L) 95 x (W) 40 x (H) 120 mm

Enclosed are a detailed description along with competitor designs for your reference.

Any further questions, please feel free to ask

```html
<!DOCTYPE html>
<html lang="en">
<head>
<meta charset="utf-8">
<title>Wavelink Earphone 5.0 – Window Box Dieline</title>
<link href="https://fonts.googleapis.com/css2?family=Comfortaa:wght@300;400;700&family=Montserrat:wght@500;600;700&family=Oswald:wght@600&display=swap" rel="stylesheet">
<style>
  :root {
    --board: #050505;
    --lime: #8be02a;
    --white: #ffffff;
    --paper: #ffffff;
    --ink-soft: #e8e8e8;
  }
  * { margin: 0; padding: 0; box-sizing: border-box; }
  html, body { width: 1200px; height: 1200px; overflow: hidden; background: var(--paper); }
  .canvas { position: relative; width: 1200px; height: 1200px; overflow: hidden; }
  .dieline { position: absolute; left: 0; top: 0; }
  .layer { position: absolute; }

  .display { font-family: "Comfortaa", sans-serif; color: var(--white); }
  .copy { font-family: "Montserrat", sans-serif; color: var(--white); }
  .lime { color: var(--lime); }

  /* corner bracket frame */
  .bracket-frame { position: absolute; }
  .bracket-frame i { position: absolute; width: 10px; height: 10px; border-color: var(--white); border-style: solid; }
  .bracket-frame .tl { left: 0; top: 0; border-width: 2px 0 0 2px; }
  .bracket-frame .tr { right: 0; top: 0; border-width: 2px 2px 0 0; }
  .bracket-frame .bl { left: 0; bottom: 0; border-width: 0 0 2px 2px; }
  .bracket-frame .br { right: 0; bottom: 0; border-width: 0 2px 2px 0; }
  .bracket-frame .company-name {
    position: absolute; inset: 0; display: flex; align-items: center; justify-content: center;
    font-family: "Comfortaa", sans-serif; font-weight: 700; color: var(--lime); letter-spacing: .5px;
  }

  /* front panel */
  .front-brand { left: 313px; top: 379px; width: 154px; height: 58px; }
  .front-brand .company-name { font-size: 17px; }
  .product-window {
    position: absolute; left: 222px; top: 451px; width: 333px; height: 155px;
    background: var(--white); border: 6px solid var(--lime); border-radius: 12px;
  }
  .front-title { left: 279px; top: 628px; }
  .front-title .line { display: block; font-size: 25px; line-height: 30px; letter-spacing: 1px; }
  .front-title .light { font-weight: 300; }
  .front-title .bold { font-weight: 400; }
  .front-version { left: 414px; top: 618px; font-size: 62px; font-weight: 700; line-height: 1; color: var(--lime); letter-spacing: -1px; }

  .badge-label {
    position: absolute; width: 70px; text-align: center;
    font-family: "Oswald", sans-serif; font-weight: 600; font-size: 9px; line-height: 10px; color: var(--board);
  }
  .powered { left: 314px; top: 795px; display: flex; align-items: center; gap: 6px; }
  .powered .lead { font-family: "Montserrat", sans-serif; font-weight: 600; font-size: 9px; color: var(--white); }
  .powered .dot { width: 11px; height: 11px; border-radius: 50%; background: var(--white); }
  .powered .name { font-family: "Montserrat", sans-serif; font-weight: 700; font-size: 14px; color: var(--white); }

  /* side panels */
  .side-title { display: flex; align-items: baseline; gap: 14px; white-space: nowrap; }
  .side-title .stack { display: flex; flex-direction: column; }
  .side-title .light { font-weight: 300; font-size: 27px; line-height: 30px; letter-spacing: 2px; }
  .side-title .bold { font-weight: 700; font-size: 27px; line-height: 30px; letter-spacing: 1px; }
  .side-title .version { font-weight: 700; font-size: 66px; color: var(--lime); line-height: 1; }
  .left-side-title { left: 122px; top: 590px; transform: translate(-50%, -50%) rotate(-90deg); }
  .left-side-title .stack { order: 0; }
  .right-side-title { left: 656px; top: 618px; transform: translate(-50%, -50%) rotate(90deg); }
  .right-brand { left: 600px; top: 401px; width: 115px; height: 46px; }
  .right-brand .company-name { font-size: 12px; }

  /* back panel */
  .spec { left: 755px; top: 370px; width: 340px; }
  .spec h3, .caution h3 { font-family: "Montserrat", sans-serif; font-weight: 700; font-size: 12px; color: var(--lime); margin-bottom: 8px; }
  .spec-table { border-collapse: collapse; font-family: "Montserrat", sans-serif; font-size: 10.5px; font-weight: 500; color: var(--white); }
  .spec-table td { padding: 0; height: 19.6px; vertical-align: middle; }
  .spec-table td.key { width: 181px; }
  .spec-table td.val { font-weight: 700; }
  .caution { left: 755px; top: 565px; width: 345px; }
  .caution h3 { margin-bottom: 5px; }
  .caution p { font-family: "Montserrat", sans-serif; font-size: 9.5px; font-weight: 500; line-height: 14px; color: var(--white); }
  .label-area { left: 755px; top: 650px; width: 158px; height: 80px; }
  .legal { left: 933px; top: 653px; width: 166px; font-family: "Montserrat", sans-serif; font-size: 7.5px; font-weight: 600; line-height: 10.5px; color: var(--ink-soft); }
  .legal .year { color: var(--lime); }
  .rule { position: absolute; left: 755px; top: 755px; width: 338px; height: 2px; background: var(--white); }
</style>
</head>
<body>
<div class="canvas">

  <svg class="dieline" width="1200" height="1200" viewBox="0 0 1200 1200" aria-hidden="true">
    <g fill="var(--board)">
      <!-- top tuck flap -->
      <path d="M202 146 L202 126 Q202 104 224 104 L553 104 Q575 104 575 126 L575 146 L575 352 L202 352 Z"/>
      <!-- dust flaps -->
      <polygon points="65,272 201,272 201,352 43,352"/>
      <polygon points="583,272 715,272 734,352 578,352"/>
      <!-- glue tab -->
      <path d="M887 352 L887 280 Q887 272 895 272 L956 272 Q964 272 964 280 L964 352 Z"/>
      <!-- side panels, front panel -->
      <rect x="43" y="352" width="158" height="476"/>
      <rect x="202" y="352" width="373" height="476"/>
      <rect x="578" y="352" width="156" height="476"/>
      <!-- back panel with bottom lock flap -->
      <path d="M737 352 L1111 352 L1160 380 L1160 800 L1111 828 L1023 951 L1023 988 Q1023 1000 1011 1000 L839 1000 Q827 1000 827 988 L827 951 L737 828 Z"/>
      <!-- bottom flaps -->
      <polygon points="43,828 201,828 201,867 117,930 43,930"/>
      <polygon points="578,828 734,828 734,930 656,930 578,867"/>
      <polygon points="202,828 575,828 575,1000 491,1000 491,947 288,947 288,1000 202,1000"/>
    </g>

    <!-- feature badges -->
    <g fill="var(--lime)">
      <polygon points="292,702 323,720 323,756 292,774 261,756 261,720"/>
      <polygon points="388,702 419,720 419,756 388,774 357,756 357,720"/>
      <polygon points="485,702 516,720 516,756 485,774 454,756 454,720"/>
    </g>
    <g fill="var(--board)">
      <circle cx="292" cy="723" r="4"/>
      <!-- speaker -->
      <polygon points="381,719 385,719 390,714 390,730 385,725 381,725"/>
      <path d="M393 718 Q396 722 393 726 M396 715 Q401 722 396 729" fill="none" stroke="var(--board)" stroke-width="1.5"/>
      <!-- microphone -->
      <rect x="482" y="712" width="6" height="11" rx="3"/>
      <path d="M479 720 Q479 727 485 727 Q491 727 491 720 M485 727 L485 731" fill="none" stroke="var(--board)" stroke-width="1.4"/>
    </g>

    <!-- certification marks, plain shapes -->
    <g fill="none" stroke="var(--white)" stroke-width="2.2">
      <rect x="757" y="781" width="24" height="24" rx="3"/>
      <circle cx="805" cy="793" r="12"/>
      <polygon points="847,781 861,805 833,805"/>
      <circle cx="885" cy="793" r="12"/>
      <rect x="914" y="781" width="18" height="24"/>
      <polygon points="957,781 970,805 944,805"/>
      <circle cx="1082" cy="793" r="12" fill="var(--white)"/>
    </g>
  </svg>

  <!-- front panel -->
  <div class="bracket-frame front-brand"><i class="tl"></i><i class="tr"></i><i class="bl"></i><i class="br"></i><span class="company-name">Company Name</span></div>
  <div class="product-window"></div>
  <div class="layer display front-title"><span class="line light">Wavelink</span><span class="line bold">Earphone</span></div>
  <div class="layer display front-version">5.0</div>
  <div class="badge-label" style="left:257px;top:734px;">Wavelink<br>5.0</div>
  <div class="badge-label" style="left:353px;top:734px;">Exceptional<br>Sound Quality</div>
  <div class="badge-label" style="left:450px;top:734px;">High Definition<br>Microphone</div>
  <div class="layer powered"><span class="lead">Powered By:</span><span class="dot"></span><span class="name">Wavelink</span></div>

  <!-- left side panel -->
  <div class="layer display side-title left-side-title">
    <span class="stack"><span class="light">Wavelink</span><span class="bold">Earphone</span></span>
    <span class="version">5.0</span>
  </div>

  <!-- right side panel -->
  <div class="bracket-frame right-brand"><i class="tl"></i><i class="tr"></i><i class="bl"></i><i class="br"></i><span class="company-name">Company Name</span></div>
  <div class="layer display side-title right-side-title">
    <span class="stack"><span class="light">Wavelink</span><span class="bold">Earphone</span></span>
    <span class="version">5.0</span>
  </div>

  <!-- back panel -->
  <div class="layer spec">
    <h3>Specification</h3>
    <table class="spec-table">
      <tr><td class="key">Wavelink Version</td><td class="val">: 5.0</td></tr>
      <tr><td class="key">Wireless Playback Duration</td><td class="val">: 3 - 4 h</td></tr>
      <tr><td class="key">Standby Time</td><td class="val">: 80 h</td></tr>
      <tr><td class="key">Wireless Range</td><td class="val">: 10 m</td></tr>
      <tr><td class="key">Impedance</td><td class="val">: 32 Ω</td></tr>
      <tr><td class="key">Sound Pressure Level</td><td class="val">: 100dB ± 3dB</td></tr>
      <tr><td class="key">Frequency Response</td><td class="val">: 20 - 20kHz</td></tr>
      <tr><td class="key">Driver Unit</td><td class="val">: 10mm</td></tr>
    </table>
  </div>
  <div class="layer caution">
    <h3>Caution</h3>
    <p>Lorem ipsum dolor sit amet, consectetur adipiscing elit. Curabitur dapibus vitae mauris consectetur fermentum. Pellentesque eleifend vel orci non tristique.</p>
  </div>
  <div class="bracket-frame label-area"><i class="tl"></i><i class="tr"></i><i class="bl"></i><i class="br"></i></div>
  <div class="layer legal"><span class="year">© 2019 Lorem ipsum dolor sit amet,</span> consectetur adipiscing elit. Curabitur dapibus vitae mauris consectetur fermentum. Pellentesque eleifend vel orci non tristique. Donec a orci luctus, bibendum leo a, hendrerit nunc.</div>
  <div class="rule"></div>

</div>
</body>
</html>
```